Book for new dads needs a cover.

We need a cover for a book titled Roadmap to Early Parenthood: Practical Methods for Welcoming a Newborn, Juggling Career and Home Life, and Managing Mental Health on the Path to Becoming a Parent. We would like to see a design that emphasizes healthy babies and confident dads.

```html
<!DOCTYPE html>
<html lang="en">
<head>
<meta charset="utf-8">
<title>Roadmap to Early Parenthood — Book Cover</title>
<link rel="stylesheet" href="https://fonts.googleapis.com/css2?family=Bebas+Neue&family=Cinzel:wght@400;700&display=swap">
<style>
  :root {
    --backdrop: #262626;
    --sky-deep: #0b4675;
    --sky-mid: #4a7a9c;
    --sky-light: #9ab8cc;
    --horizon-pale: #d8d0a8;
    --horizon-warm: #f4c983;
    --horizon-amber: #e6b062;
    --ground: #000000;
    --white: #ffffff;
    --gold-dark: #a8832e;
    --gold-light: #e4ca7a;
    --gold-author: #e0c271;
  }
  * { margin: 0; padding: 0; box-sizing: border-box; }
  html, body {
    width: 1200px;
    height: 1200px;
    overflow: hidden;
    background: var(--backdrop);
  }
  .book-cover {
    position: absolute;
    left: 217px;
    top: 26px;
    width: 765px;
    height: 1148px;
    overflow: hidden;
    background: var(--ground);
  }
  .cover-photo {
    position: absolute;
    inset: 0;
    background:
      radial-gradient(ellipse 55% 30% at 55% 48%, rgba(200, 220, 235, 0.55), rgba(200, 220, 235, 0) 70%),
      linear-gradient(180deg,
        var(--sky-deep) 0%,
        var(--sky-mid) 28%,
        var(--sky-light) 44%,
        var(--horizon-pale) 56%,
        var(--horizon-warm) 64%,
        var(--horizon-amber) 69%,
        #1b160e 72%,
        var(--ground) 78%,
        var(--ground) 100%);
  }
  .cover-type {
    position: absolute;
    inset: 0;
    width: 765px;
    height: 1148px;
  }
  .title-line {
    font-family: 'Bebas Neue', 'Oswald', sans-serif;
  }
  .title-accent { fill: url(#gold-sheen); }
  .title-main { fill: var(--white); }
  .subtitle {
    position: absolute;
    left: 0;
    right: 0;
    top: 866px;
    text-align: center;
    font-family: 'Cinzel', 'Trajan Pro', serif;
    color: var(--white);
    letter-spacing: 0.5px;
  }
  .subtitle-lead {
    display: block;
    font-weight: 700;
    font-size: 22px;
    line-height: 30px;
  }
  .subtitle-rest {
    display: block;
    font-weight: 400;
    font-size: 18.5px;
    line-height: 28px;
    padding: 0 70px;
  }
  .author-name { fill: var(--gold-author); font-family: 'Bebas Neue', 'Oswald', sans-serif; }
</style>
</head>
<body>
  <div class="book-cover">
    <div class="cover-photo" role="img" aria-label="Silhouette of a father crouching with open arms as his toddler walks toward him on a grassy hill, against a blue sky fading into a golden sunset"></div>

    <svg class="cover-type" viewBox="0 0 765 1148" aria-labelledby="cover-title">
      <defs>
        <linearGradient id="gold-sheen" x1="0" y1="0" x2="1" y2="0">
          <stop offset="0" stop-color="var(--gold-dark)"/>
          <stop offset="0.5" stop-color="var(--gold-light)"/>
          <stop offset="1" stop-color="var(--gold-dark)"/>
        </linearGradient>
      </defs>
      <text id="cover-title" class="title-line title-accent" x="69" y="254" font-size="254" textLength="631" lengthAdjust="spacingAndGlyphs">ROADMAP</text>
      <text class="title-line title-main" x="50" y="374" font-size="146" textLength="671" lengthAdjust="spacingAndGlyphs">TO EARLY</text>
      <text class="title-line title-main" x="50" y="580" font-size="230" textLength="671" lengthAdjust="spacingAndGlyphs">PARENTHOOD</text>
      <text class="author-name" x="70" y="1098" font-size="116" textLength="637" lengthAdjust="spacing">AUTHOR NAME</text>
    </svg>

    <p class="subtitle">
      <span class="subtitle-lead">Practical Methods for Welcoming a Newborn,</span>
      <span class="subtitle-rest">Juggling Career and Home Life, and Managing Mental Health on the Path to Becoming a Parent.</span>
    </p>
  </div>
</body>
</html>
```